Ravnaas-Lilleby Group AS

We need a design for our company including background pictures on our web (wix-template), redesign of logo and reports. Our company delivers personality test and services to clients when hiring staff or related to organizatonal developement.

Target Market(s)

Unisex, Age 30-50, managers in private corporations

Industry/Entity Type

Recruitment

Logo Text

Bygger laget sterkt (english translate: buids your team strong)

Number of Pages Required

1 page

Font styles to use
Sans Serif

Colors
add136
34a6d7
0255a3

Requirements
Must have
• The ideal designer will be the one to bring my narrative come to life. And it will have to include the testresults report and redesign (!) of my logo. Following the attached brief in ppt:
• - the testresult report
• - redesign logo
• - graphic elements in a maritime narrative
• - including the boat, the radar, 7 GULLs, the compass etc
Nice to have
• A strong narrative with a lot of elements.
• I really like the green color in the attached breif ;-)

```html
<!DOCTYPE html>
<html lang="en">
<head>
<meta charset="utf-8">
<title>Ravnaas-Lilleby Group AS – Arbeidsstiler</title>
<link href="https://fonts.googleapis.com/css2?family=Roboto:wght@400;500;700&display=swap" rel="stylesheet">
<style>
:root{
  --mint:#eefbe9;
  --hero-top:#eaf9e4;
  --hero-ground:#b9d9b4;
  --band:#6c706b;
  --ink:#222;
  --muted:#555;
  --navy:#1f3a93;
  --green:#2e9a3f;
  --red:#e5333f;
  --footer:#1c1c1c;
  --footer-text:#e6e6e6;
  --blue:#3a6fb8;
}
*{box-sizing:border-box;margin:0;padding:0}
html,body{width:1200px;height:2651px;overflow:hidden}
body{font-family:'Roboto',sans-serif;color:var(--ink);background:#fff;position:relative}
.abs{position:absolute}
.top-strip{left:0;top:0;width:1200px;height:50px;background:var(--mint)}
.site-header{left:0;top:50px;width:1200px;height:81px;background:#fff;box-shadow:0 2px 4px rgba(0,0,0,.06)}
.brand{left:92px;top:18px;display:flex;align-items:center;gap:10px}
.brand-name{font-weight:700;font-size:30px;color:var(--navy);letter-spacing:1px}
.brand-square{width:14px;height:14px;background:var(--navy)}
.nav{left:392px;top:29px;display:flex;gap:0;font-size:16px;font-weight:500;color:#222}
.nav a{color:inherit;text-decoration:none;position:absolute;white-space:nowrap}
.lang{left:1000px;top:30px;display:flex;align-items:center;gap:8px;font-size:16px}
.flag{width:20px;height:12px;background:#2b4a9b;position:relative}
.hero{left:0;top:131px;width:1200px;height:434px;background:linear-gradient(180deg,var(--hero-top) 0%,#e4f5dd 75%,var(--hero-ground) 100%)}
.band{left:0;width:1200px;height:114px;background:var(--band);color:#fff}
.band-item{position:absolute;top:18px;display:flex;gap:16px}
.band-item h3{font-size:17px;font-weight:500;margin-bottom:10px}
.band-item p{font-size:13px;line-height:1.45;color:#e9e9e9;width:230px}
.band-divider{position:absolute;top:14px;width:1px;height:86px;background:#8f938e}
.section-title{left:0;top:748px;width:1200px;text-align:center;font-size:35px;font-weight:700}
.compass{left:470px;top:928px;width:272px;height:272px;border-radius:50%;background:radial-gradient(circle,#fff 0%,#fff 55%,#e9eef6 70%,#3a6fb8 72%,#fff 76%)}
.dir{font-size:34px;font-weight:500}
.legend{left:937px;top:984px;font-size:17px;color:#666;line-height:42.5px}
.legend b{font-weight:400;color:#333;display:inline-block;width:34px}
.meter-label{font-size:20px;font-weight:700;text-align:center;width:300px}
.scale{font-size:13px;color:#333}
.io-title{font-size:21px;font-weight:700;display:flex;align-items:center;gap:12px}
.col-head{font-size:14px;font-weight:500;text-align:center}
.grid{display:grid;grid-template-columns:120px 120px;grid-auto-rows:45.3px;gap:0}
.cell{display:flex;align-items:center;justify-content:center;color:#fff;font-size:14px;font-weight:500;border:1px solid rgba(255,255,255,.6)}
.yes{background:var(--green)}
.no{background:var(--red)}
.score{left:548px;top:1612px;width:106px;font-size:15px;color:#333}
.score div{height:45.3px;display:flex;align-items:center;justify-content:center;letter-spacing:1px}
.score span{font-size:17px;margin:0 8px}
.profile{left:0;top:1930px;width:1200px;font-size:15px}
.profile .row{position:absolute;display:flex}
.profile .label{position:absolute;right:612px;white-space:nowrap;color:#333}
.profile .value{position:absolute;left:622px;width:420px;line-height:1.6;color:#222}
.site-footer{left:0;top:2287px;width:1200px;height:364px;background:var(--footer);color:var(--footer-text)}
.site-footer h4{position:absolute;top:70px;font-size:19px;font-weight:700;color:#fff;letter-spacing:.3px}
.about{position:absolute;left:99px;top:114px;width:410px;font-size:14px;line-height:1.72}
.social{position:absolute;left:99px;top:208px;display:flex;gap:10px}
.social span{width:32px;height:32px;border:1px solid #bbb;border-radius:50%}
.links{position:absolute;left:576px;top:112px;list-style:none;font-size:12.5px;line-height:24.8px}
.contact{position:absolute;left:797px;top:112px;font-size:12.5px;line-height:1.7}
.contact li{list-style:none;display:flex;gap:18px;margin-bottom:16px}
.contact svg{flex:none;margin-top:3px}
.footer-rule{position:absolute;left:99px;top:295px;width:1002px;height:1px;background:#333}
.copyright{position:absolute;left:0;top:321px;width:1200px;text-align:center;font-size:12.5px}
</style>
</head>
<body>
<div class="abs top-strip"></div>

<header class="abs site-header">
  <div class="abs brand"><span class="brand-square"></span><span class="brand-name">RLG</span></div>
  <nav class="abs nav">
    <a style="left:0">Take the PAT test</a>
    <a style="left:168px">product Presentation</a>
    <a style="left:361px">Company Presentation</a>
  </nav>
  <svg class="abs" style="left:955px;top:30px" width="18" height="18" viewBox="0 0 18 18"><circle cx="7" cy="7" r="5" fill="none" stroke="#222" stroke-width="2.4"/><line x1="11" y1="11" x2="16" y2="16" stroke="#222" stroke-width="2.6"/></svg>
  <div class="abs lang"><span class="flag"></span><span>English</span><svg width="10" height="6" viewBox="0 0 10 6"><path d="M0 0h10L5 6z" fill="#222"/></svg></div>
</header>

<div class="abs hero" role="img" aria-label="Hero illustration: a row of sketched figures holding unhappy emoji signs on a light green meadow"></div>

<section class="abs band" style="top:565px">
  <div class="band-item" style="left:97px">
    <svg width="52" height="46" viewBox="0 0 52 46"><circle cx="26" cy="12" r="8" fill="#fff"/><circle cx="10" cy="16" r="6" fill="#fff"/><circle cx="42" cy="16" r="6" fill="#fff"/><path d="M12 44c0-12 6-20 14-20s14 8 14 20z" fill="#fff"/><path d="M0 40c0-10 4-16 10-16 3 0 5 1 7 3-3 4-5 8-5 13z" fill="#fff"/><path d="M52 40c0-10-4-16-10-16-3 0-5 1-7 3 3 4 5 8 5 13z" fill="#fff"/></svg>
    <div><h3>Recruitment</h3><p>We are nationwide including through cooperation agreements.</p></div>
  </div>
  <div class="band-divider" style="left:420px"></div>
  <div class="band-item" style="left:450px">
    <svg width="52" height="46" viewBox="0 0 52 46"><circle cx="18" cy="26" r="12" fill="none" stroke="#fff" stroke-width="7" stroke-dasharray="5 3"/><circle cx="18" cy="26" r="4" fill="#fff"/><circle cx="40" cy="12" r="7" fill="none" stroke="#fff" stroke-width="5" stroke-dasharray="3 2"/></svg>
    <div><h3>Organizational development</h3><p>We are nationwide including through cooperation agreements.</p></div>
  </div>
  <div class="band-divider" style="left:785px"></div>
  <div class="band-item" style="left:818px">
    <svg width="40" height="46" viewBox="0 0 40 46"><circle cx="20" cy="12" r="10" fill="#fff"/><path d="M2 44c0-13 8-20 18-20s18 7 18 20z" fill="#fff"/></svg>
    <div><h3>Personality test</h3><p>We are nationwide including through cooperation agreements.</p></div>
  </div>
</section>

<h1 class="abs section-title">Arbeidsstiler</h1>

<div class="abs dir" style="left:594px;top:840px">N</div>
<div class="abs dir" style="left:595px;top:1246px">S</div>
<div class="abs dir" style="left:387px;top:1042px">W</div>
<div class="abs dir" style="left:792px;top:1042px">E</div>
<div class="abs compass" role="img" aria-label="Compass rose illustration with a red needle pointing north-east"></div>

<div class="abs legend">
  <div><b>N</b>Navigator</div>
  <div><b>W</b>Worker</div>
  <div><b>S</b>Integrator</div>
  <div><b>E</b>Dicipline</div>
</div>

<div class="abs meter-label" style="left:276px;top:1309px">ENERGI</div>
<svg class="abs" style="left:336px;top:1355px" width="190" height="48" viewBox="0 0 190 48">
  <rect x="1.5" y="1.5" width="176" height="45" rx="3" fill="#fff" stroke="#888" stroke-width="3"/>
  <rect x="178" y="16" width="8" height="16" fill="#888"/>
  <g fill="var(--green)"><rect x="8" y="7" width="5" height="34"/><rect x="16" y="7" width="5" height="34"/><rect x="24" y="7" width="5" height="34"/><rect x="32" y="7" width="5" height="34"/><rect x="40" y="7" width="5" height="34"/><rect x="48" y="7" width="5" height="34"/><rect x="56" y="7" width="5" height="34"/><rect x="64" y="7" width="5" height="34"/><rect x="72" y="7" width="5" height="34"/><rect x="80" y="7" width="5" height="34"/></g>
  <g fill="var(--red)"><rect x="88" y="7" width="5" height="34"/><rect x="96" y="7" width="5" height="34"/><rect x="104" y="7" width="5" height="34"/><rect x="112" y="7" width="5" height="34"/><rect x="120" y="7" width="5" height="34"/></g>
</svg>
<div class="abs scale" style="left:334px;top:1412px">0</div>
<div class="abs scale" style="left:493px;top:1412px">100</div>

<div class="abs meter-label" style="left:619px;top:1309px">PROBLEMLØSNINGSEVNE</div>
<svg class="abs" style="left:679px;top:1355px" width="190" height="48" viewBox="0 0 190 48">
  <rect x="1.5" y="1.5" width="176" height="45" rx="3" fill="#fff" stroke="#888" stroke-width="3"/>
  <rect x="178" y="16" width="8" height="16" fill="#888"/>
  <g fill="var(--green)"><rect x="8" y="7" width="5" height="34"/><rect x="16" y="7" width="5" height="34"/><rect x="24" y="7" width="5" height="34"/><rect x="32" y="7" width="5" height="34"/><rect x="40" y="7" width="5" height="34"/><rect x="48" y="7" width="5" height="34"/><rect x="56" y="7" width="5" height="34"/><rect x="64" y="7" width="5" height="34"/><rect x="72" y="7" width="5" height="34"/><rect x="80" y="7" width="5" height="34"/></g>
  <g fill="var(--red)"><rect x="88" y="7" width="5" height="34"/><rect x="96" y="7" width="5" height="34"/><rect x="104" y="7" width="5" height="34"/><rect x="112" y="7" width="5" height="34"/><rect x="120" y="7" width="5" height="34"/></g>
</svg>
<div class="abs scale" style="left:677px;top:1412px">0</div>
<div class="abs scale" style="left:836px;top:1412px">100</div>

<div class="abs io-title" style="left:266px;top:1477px">
  <svg width="54" height="54" viewBox="0 0 54 54"><circle cx="27" cy="27" r="24" fill="none" stroke="var(--navy)" stroke-width="4"/><circle cx="27" cy="27" r="15" fill="none" stroke="var(--navy)" stroke-width="3"/><circle cx="27" cy="27" r="6" fill="var(--navy)"/><line x1="27" y1="27" x2="44" y2="12" stroke="var(--navy)" stroke-width="3"/></svg>
  LYTTE
</div>
<div class="abs io-title" style="left:692px;top:1482px">
  <svg width="48" height="44" viewBox="0 0 48 44"><path d="M4 14h10l22-12v38L14 28H4z" fill="var(--navy)"/><rect x="10" y="28" width="8" height="14" fill="var(--navy)"/><rect x="40" y="16" width="6" height="10" fill="var(--navy)"/></svg>
  SENDE
</div>

<div class="abs col-head" style="left:270px;top:1575px;width:120px">Empati</div>
<div class="abs col-head" style="left:389px;top:1575px;width:120px">Profesjonell</div>
<div class="abs col-head" style="left:672px;top:1575px;width:162px">Overbevisningsevne</div>
<div class="abs col-head" style="left:813px;top:1575px;width:120px">Autoritet</div>

<div class="abs grid" style="left:270px;top:1612px">
  <div class="cell no">NO</div><div class="cell no">NO</div>
  <div class="cell yes">YES</div><div class="cell no">NO</div>
  <div class="cell yes">YES</div><div class="cell no">NO</div>
  <div class="cell yes">YES</div><div class="cell no">NO</div>
  <div class="cell yes">YES</div><div class="cell yes">YES</div>
  <div class="cell yes">YES</div><div class="cell yes">YES</div>
</div>

<div class="abs score">
  <div>------<span>1</span>------</div>
  <div>------<span>2</span>------</div>
  <div>------<span>2</span>------</div>
  <div>------<span>1</span>------</div>
  <div>------<span>4</span>------</div>
  <div>------<span>5</span>------</div>
</div>

<div class="abs grid" style="left:693px;top:1612px">
  <div class="cell no">NO</div><div class="cell no">NO</div>
  <div class="cell no">NO</div><div class="cell no">NO</div>
  <div class="cell no">NO</div><div class="cell no">NO</div>
  <div class="cell yes">YES</div><div class="cell no">NO</div>
  <div class="cell yes">YES</div><div class="cell no">NO</div>
  <div class="cell yes">YES</div><div class="cell yes">YES</div>
</div>

<div class="abs profile">
  <div class="label" style="top:0">Name :</div><div class="value" style="top:0">John Doe</div>
  <div class="label" style="top:48px">Company :</div><div class="value" style="top:48px">Finibus Bonorum et Malo</div>
  <div class="label" style="top:97px">Profile :</div><div class="value" style="top:97px">At vero eos et accusamus et iusto odio dignissimos ducimus qui blanditiis praesentium voluptatum deleniti atque corrupti quos dolores</div>
</div>

<section class="abs band" style="top:2172px;height:115px">
  <div class="band-item" style="left:97px">
    <svg width="48" height="44" viewBox="0 0 48 44"><path d="M4 14h10l22-12v38L14 28H4z" fill="#fff"/><rect x="10" y="28" width="8" height="14" fill="#fff"/></svg>
    <div><h3>Send</h3><p>We are nationwide including through cooperation agreements.</p></div>
  </div>
  <div class="band-divider" style="left:420px"></div>
  <div class="band-item" style="left:450px">
    <svg width="52" height="52" viewBox="0 0 54 54"><circle cx="27" cy="27" r="24" fill="none" stroke="#fff" stroke-width="4"/><circle cx="27" cy="27" r="15" fill="none" stroke="#fff" stroke-width="3"/><circle cx="27" cy="27" r="6" fill="#fff"/><line x1="27" y1="27" x2="44" y2="12" stroke="#fff" stroke-width="3"/></svg>
    <div><h3>Receive</h3><p>We are nationwide including through cooperation agreements.</p></div>
  </div>
  <div class="band-divider" style="left:785px"></div>
  <div class="band-item" style="left:810px">
    <svg width="52" height="50" viewBox="0 0 52 50"><rect x="20" y="2" width="12" height="10" fill="#fff"/><rect x="12" y="14" width="28" height="10" fill="#fff"/><path d="M2 26h48l-8 14H10z" fill="#fff"/><path d="M2 46q6-4 12 0t12 0 12 0 12 0" fill="none" stroke="#fff" stroke-width="2.5"/></svg>
    <div><h3>Clients business</h3><p>We are nationwide including through cooperation agreements.</p></div>
  </div>
</section>

<footer class="abs site-footer">
  <h4 style="left:99px">RAVNAAS-LILLEBY GROUP AS</h4>
  <p class="about">Ravnaas-Lilleby Group as (RLG) is an active counselor nationally and internationally in the field of recruitment and organizational development / change.</p>
  <div class="social"><span></span><span></span><span></span></div>

  <h4 style="left:576px">QUICK LINKS</h4>
  <ul class="links">
    <li>Help</li><li>FAQ</li><li>Support</li><li>Sitemap</li><li>Terms Of Use</li><li>Privacy Statement</li>
  </ul>

  <h4 style="left:797px">CONTACT US</h4>
  <ul class="contact">
    <li><svg width="12" height="16" viewBox="0 0 12 16"><path d="M6 0a6 6 0 0 1 6 6c0 4-6 10-6 10S0 10 0 6a6 6 0 0 1 6-6z" fill="#fff"/><circle cx="6" cy="6" r="2.2" fill="var(--footer)"/></svg><span>Strandveien 42, 2nd floor,<br>0250 Oslo</span></li>
    <li style="margin-top:6px"><svg width="14" height="14" viewBox="0 0 14 14"><path d="M3 0l3 3-2 2c1 2 3 4 5 5l2-2 3 3-2 3C6 14 0 8 0 3z" fill="#fff"/></svg><span>21 38 90 14</span></li>
    <li><svg width="15" height="11" viewBox="0 0 15 11"><rect width="15" height="11" fill="#fff"/><path d="M0 0l7.5 6L15 0" fill="none" stroke="var(--footer)" stroke-width="1.5"/></svg><span>post@ravnaas-lilleby.no</span></li>
  </ul>

  <div class="footer-rule"></div>
  <p class="copyright">Copyrights © 2017, Ravnaas-Lilleby Group . All rights reserved.</p>
</footer>
</body>
</html>
```